Wren of Fabrics relaunch: brand, logo and website redesign

Wren of Fabrics www.wrenoffabrics.com is relaunching to focus on empowering style advice, e books and courses.
We need a new logo, brand identity and website which reflects this change.
The structure of the site and pages have been completed http://dev1.wrenoffabrics.com/
but we need to update the brand look and feel
Please read the full brief, uploaded, before submitting your designs.

Target Market(s)

Women, primarily aged 28-45, English speaking USA and UK
Ambitious and determined. Looking for solutions. Open to self-improvement.
Maybe not as confident with style and body image as other parts of their life.

Logo Text

Brand name Wren of Fabrics Strapline version 1: Unlock your personal best Strapline version 2: Unlock better Logo/graphical icon for use with/without text

Number of Pages Required

3 page

Font styles to use
Sans Serif

Requirements
Must have
• 1. Web designs for home page, a channel page and advice page (see attached brief)
Web designs must be consistent with new website design navigation, and page structure http://dev1.wrenoffabrics.com/
2. Web style guide to include colour palettes/system; web fonts, icons, illustrations and guidelines/examples free stock photography. see Mindmap upload for example of colour pallette we like.
Nice to have
• Ebook front covers
Quiz promotions
Course promotions
Other web pages
Social media pages eg Pagebook, Snapgrid,Chirpline
Should not have
• Paid photography or photos where don’t have the rights

```html
<!DOCTYPE html>
<html lang="en">
<head>
<meta charset="utf-8">
<title>Wren of Fabrics — Blog</title>
<link href="https://fonts.googleapis.com/css2?family=Italiana&family=DM+Sans:wght@400;500;700&family=Dancing+Script:wght@500&display=swap" rel="stylesheet">
<style>
:root{
  --navy:#1b2a4a;
  --orange:#f0883a;
  --yellow:#fbd03e;
  --mist:#f7f8fb;
  --white:#ffffff;
  --text:#2a3350;
  --display:"Italiana", serif;
  --sans:"DM Sans", sans-serif;
}
*{margin:0;padding:0;box-sizing:border-box}
html,body{width:1200px;height:2488px;overflow:hidden}
body{position:relative;background:var(--white);font-family:var(--sans);color:var(--text)}
.abs{position:absolute}
.top-band{left:0;top:0;width:1200px;height:585px;background:var(--mist)}
.footer-band{left:0;top:2045px;width:1200px;height:443px;background:var(--mist)}

.brand{left:87px;display:flex;align-items:center;gap:10px}
.brand-mark{width:14px;height:14px;background:var(--navy)}
.brand-name{font-family:var(--sans);font-weight:500;font-size:20px;color:var(--navy);white-space:nowrap;line-height:1}

.nav{top:80px;left:549px;font-size:14px;color:var(--navy)}
.nav a{color:inherit;text-decoration:none;position:absolute;white-space:nowrap}
.cart{left:1069px;top:69px;width:43px;height:43px;border-radius:50%;background:var(--navy)}
.cart-badge{left:1096px;top:64px;width:15px;height:15px;border-radius:50%;background:var(--orange);color:#fff;font-size:8px;text-align:center;line-height:15px}

.kicker{left:87px;top:250px;font-family:var(--display);font-size:27px;color:var(--navy)}
.page-title{left:85px;top:278px;font-family:var(--display);font-weight:400;font-size:88px;color:var(--yellow);line-height:1}
.featured-note{left:982px;top:281px;font-family:"Dancing Script",cursive;font-size:19px;color:var(--yellow)}

.hero{left:87px;top:445px;width:1026px;height:342px;background:linear-gradient(100deg,#6b4a38 0%,#b44a2a 30%,#c9b9a8 45%,#8a3a22 60%,#2c2a33 78%,#b5532b 100%)}
.badge{left:140px;top:497px;width:174px;height:54px;background:var(--yellow);display:flex;align-items:center;padding-left:30px;gap:12px;color:#fff;font-size:10.5px;font-weight:500}
.badge i{width:26px;height:26px;border:1px solid rgba(255,255,255,.8);border-radius:50%;display:block}

.lead-date{left:87px;top:842px;font-size:16px;color:var(--orange);font-weight:500}
.lead-title{left:87px;top:882px;font-family:var(--display);font-weight:400;font-size:60px;color:var(--navy);white-space:nowrap;line-height:1.1}
.lead-copy{top:987px;width:450px;font-size:13px;line-height:29px;color:var(--navy)}

.card-img{width:335px;height:208px}
.card-date{font-size:10px;color:var(--orange);font-weight:500}
.card-title{width:335px;font-family:var(--display);font-weight:400;font-size:25px;line-height:30px;color:var(--navy)}

.f-head{font-size:13px;font-weight:500;color:var(--navy)}
.f-item{font-size:13px;color:var(--navy)}
.call{left:624px;top:2258px;width:191px;height:38px;background:#fff;border-radius:6px;box-shadow:0 4px 14px rgba(27,42,74,.06);display:flex;align-items:center;padding-left:14px;gap:8px}
.call-dot{width:14px;height:14px;border-radius:50%;background:#2cc4c9}
.call small{font-size:6px;color:var(--navy)}
.call b{font-size:10px;letter-spacing:2px;color:var(--navy);font-weight:500}
.social{width:44px;height:44px;border-radius:50%;background:var(--navy)}
.social.hot{background:var(--orange);box-shadow:0 6px 14px rgba(240,136,58,.45)}
.copy{left:0;width:1200px;text-align:center;color:var(--navy)}
</style>
</head>
<body>
<div class="abs top-band"></div>
<div class="abs footer-band"></div>

<header>
  <div class="abs brand" style="top:80px">
    <span class="brand-mark"></span>
    <span class="brand-name">Wren of Fabrics</span>
  </div>
  <nav class="abs nav">
    <a style="left:0">Advice</a><a style="left:77px">Courses</a><a style="left:161px">Quizzes</a>
    <a style="left:244px">Ebooks</a><a style="left:323px">About</a><a style="left:395px">Blog</a>
  </nav>
  <svg class="abs" style="left:1022px;top:83px" width="14" height="14" viewBox="0 0 14 14" aria-label="Search"><circle cx="5.5" cy="5.5" r="4" fill="none" stroke="#1b2a4a" stroke-width="1.4"/><line x1="8.5" y1="8.5" x2="12.5" y2="12.5" stroke="#1b2a4a" stroke-width="1.4"/></svg>
  <div class="abs cart"></div>
  <svg class="abs" style="left:1083px;top:81px" width="15" height="17" viewBox="0 0 15 17" aria-label="Cart"><rect x="1" y="5" width="13" height="11" fill="none" stroke="#fff" stroke-width="1.4"/><path d="M4.5 7V4a3 3 0 0 1 6 0v3" fill="none" stroke="#fff" stroke-width="1.4"/></svg>
  <div class="abs cart-badge">1</div>
</header>

<main>
  <div class="abs kicker">Latest articles</div>
  <h1 class="abs page-title">Blog</h1>
  <div class="abs featured-note">Featured Artical</div>
  <svg class="abs" style="left:940px;top:308px" width="40" height="50" viewBox="0 0 40 50"><path d="M36 4 C20 6 10 18 12 40" fill="none" stroke="#fbd03e" stroke-width="1.6"/><path d="M7 34 L12 42 L17 35" fill="none" stroke="#fbd03e" stroke-width="1.6"/></svg>

  <div class="abs hero" role="img" aria-label="Hands browsing a rail of colourful patterned dresses"></div>
  <div class="abs badge"><i></i>Featured artical</div>

  <div class="abs lead-date">September 20, 2020.</div>
  <h2 class="abs lead-title">Top shopping Tips, work from home</h2>
  <p class="abs lead-copy" style="left:87px">Lorem ipsum dolor sit amet, consetetur sadipscing elitr, sed diam nonumy eirmod tempor invidunt ut labore et dolore magna aliquyam erat, sed diam voluptua. At vero eos et accusam et justo duo dolores et ea rebum.</p>
  <p class="abs lead-copy" style="left:600px">Lorem ipsum dolor sit amet, consetetur sadipscing elitr, sed diam nonumy eirmod tempor invidunt ut labore et dolore magna aliquyam erat, sed diam voluptua. At vero eos et accusam et justo duo dolores et ea rebum.</p>

  <section>
    <div class="abs card-img" style="left:87px;top:1200px;background:linear-gradient(120deg,#e4e2df,#c9c4c0 50%,#6a2530 70%,#d9d6d3)" role="img" aria-label="Woman carrying shopping bags"></div>
    <div class="abs card-img" style="left:433px;top:1200px;background:linear-gradient(180deg,#4f86c0,#a9c6e2 60%,#9fb9d6)" role="img" aria-label="Woman in a light blue dress against a sky"></div>
    <div class="abs card-img" style="left:779px;top:1200px;background:linear-gradient(100deg,#d9dde2,#b7bcc2 40%,#4b3a33 65%,#7a3a4c)" role="img" aria-label="Clothing rail on a street"></div>
    <div class="abs card-date" style="left:87px;top:1444px">September 20, 2020.</div>
    <div class="abs card-date" style="left:433px;top:1444px">September 20, 2020.</div>
    <div class="abs card-date" style="left:777px;top:1444px">June 13, 2020.</div>
    <h3 class="abs card-title" style="left:87px;top:1467px">Top shopping Tips: Making<br>it work from home.</h3>
    <h3 class="abs card-title" style="left:433px;top:1467px">Duchess of Avonmere<br>dressed in electric dress !</h3>
    <h3 class="abs card-title" style="left:779px;top:1467px">How to dress right for your<br>age during the festive !</h3>

    <div class="abs card-img" style="left:87px;top:1624px;background:linear-gradient(120deg,#4c5d78,#7b8aa2 45%,#3f4f6a)" role="img" aria-label="Two friends in denim holding flowers"></div>
    <div class="abs card-img" style="left:433px;top:1624px;background:linear-gradient(180deg,#e7e4df,#d2cfca 60%,#a8a6a4)" role="img" aria-label="Four women laughing together"></div>
    <div class="abs card-img" style="left:779px;top:1624px;background:linear-gradient(180deg,#8a5a48,#7d5545 55%,#7f8a48 70%,#6f7d3c)" role="img" aria-label="Painted brick wall above a grass field"></div>
    <div class="abs card-date" style="left:87px;top:1868px">September 20, 2020.</div>
    <div class="abs card-date" style="left:433px;top:1868px">September 20, 2020.</div>
    <div class="abs card-date" style="left:777px;top:1868px">June 13, 2020.</div>
    <h3 class="abs card-title" style="left:87px;top:1891px">Styling For Women After<br>40 With Fashionating Life</h3>
    <h3 class="abs card-title" style="left:433px;top:1891px">How to dress right for your<br>age during the festive !</h3>
    <h3 class="abs card-title" style="left:779px;top:1891px">Why protecting, promoting<br>essential services women</h3>
  </section>
</main>

<footer>
  <div class="abs brand" style="top:2188px">
    <span class="brand-mark"></span>
    <span class="brand-name">Wren of Fabrics</span>
  </div>
  <div class="abs f-head" style="left:374px;top:2156px">Navigation</div>
  <div class="abs f-item" style="left:374px;top:2188px">Home</div>
  <div class="abs f-item" style="left:374px;top:2217px">Advice</div>
  <div class="abs f-item" style="left:374px;top:2246px">About</div>
  <div class="abs f-item" style="left:374px;top:2275px">Contact</div>
  <div class="abs f-head" style="left:499px;top:2156px">Product</div>
  <div class="abs f-item" style="left:499px;top:2188px">Courses</div>
  <div class="abs f-item" style="left:499px;top:2217px">Quizzes</div>
  <div class="abs f-item" style="left:499px;top:2246px">Ebooks</div>
  <div class="abs f-item" style="left:499px;top:2275px">Blog</div>
  <div class="abs f-head" style="left:624px;top:2156px">Place</div>
  <div class="abs f-item" style="left:624px;top:2188px">24/9 Linden Row, Marlow Bay QLD 4190</div>
  <div class="abs f-item" style="left:624px;top:2215px">hello@wrenoffabrics.com</div>
  <div class="abs call"><span class="call-dot"></span><small>Call us on</small><b>0412-555-087</b></div>
  <div class="abs f-head" style="left:895px;top:2156px">Social Media</div>
  <div class="abs social" style="left:895px;top:2200px" role="img" aria-label="Pagebook"></div>
  <div class="abs social hot" style="left:956px;top:2200px" role="img" aria-label="Snapgrid"></div>
  <div class="abs social" style="left:1013px;top:2200px" role="img" aria-label="Reelhall"></div>

  <div class="abs copy" style="top:2420px;font-size:10.5px">© Wren of Fabrics Company - All Rights Reserved</div>
  <div class="abs copy" style="top:2441px;font-size:7.5px">Terms &amp; Conditions | Privacy Policy | | Contact Us</div>
</footer>
</body>
</html>
```